NEW Modern Sleek Business Card for VR Language Startup

Our startup is using VR to lead the next wave of world language education. We need a two-sided business card that introduces the larger organization (Brightloom Language Inc) and our contact info on one side and shows the product, Glimwoorld, on the other side.

Side 1 (contact info)= Brightloom Logo and Contact info (name, title, phone, email)

Side 2 (product)= Glimworld logo, text, and website
Text= Culturally Immersive Language Learning Games
Website= www.glimworld-play.com

Target Market(s)

Education, Technology

Contact Information for Business Card

Contact info will be updated upon approval of the design. For now, put this as a placeholder.

Perry Dunmore
Founder & CEO
pdunmore@quillpost-mail.net
(555)-014-2286

Font styles to use
Other font styles liked:
• Gibson and Century Gothic are the brand fonts

Requirements
Nice to have
• I would love to see cohesion between the design and colors of the two logos. I have attached a few business card designs that I like, so you can get a feel for my preferred style.

```html
<!DOCTYPE html>
<html lang="en">
<head>
<meta charset="utf-8">
<title>Brightloom Language – Business Card</title>
<link href="https://fonts.googleapis.com/css2?family=Roboto:wght@400;500;700&display=swap" rel="stylesheet">
<style>
  :root {
    --backdrop: #c9cdcf;
    --card-paper: #f4f3f1;
    --ink-dark: #1f1f22;
    --ink-mid: #4a4a4f;
    --brand-blue: #2f8cf0;
    --brand-orange: #f07a2a;
    --brand-violet: #3a46d8;
    --brand-teal: #19a6c0;
    --divider: #d6d5d2;
  }
  * { box-sizing: border-box; margin: 0; padding: 0; }
  html, body {
    width: 1200px; height: 824px; overflow: hidden;
    background: var(--backdrop);
    font-family: "Roboto", Arial, sans-serif;
  }
  .canvas {
    width: 1200px; height: 824px;
    display: flex; align-items: center; justify-content: center; gap: 48px;
  }
  .card {
    width: 520px; height: 297px;
    background: var(--card-paper);
    border-radius: 4px;
    box-shadow: 0 10px 24px rgba(0,0,0,0.12);
    position: relative;
  }

  /* Contact side */
  .card-contact { display: flex; align-items: center; }
  .company-block {
    width: 52%; height: 100%;
    display: flex; flex-direction: column; align-items: center; justify-content: center; gap: 10px;
  }
  .company-mark {
    width: 46px; height: 46px; border-radius: 50%;
    background: linear-gradient(135deg, var(--brand-orange), #e23a8a 55%, var(--brand-blue));
  }
  .company-name {
    font-size: 30px; font-weight: 500; letter-spacing: 3px;
    color: var(--ink-dark);
  }
  .company-sub {
    font-size: 12px; font-weight: 400; letter-spacing: 9px;
    color: var(--ink-mid); text-transform: uppercase;
  }
  .card-divider {
    width: 1px; height: 150px; background: var(--divider);
  }
  .contact-block { padding-left: 28px; }
  .person-name { font-size: 22px; font-weight: 500; color: var(--brand-blue); }
  .person-title { font-size: 15px; font-weight: 500; color: var(--brand-orange); margin-top: 2px; }
  .contact-list { list-style: none; margin-top: 16px; }
  .contact-list li {
    display: flex; align-items: center; gap: 8px;
    font-size: 13px; color: var(--ink-mid); margin-bottom: 6px;
  }
  .contact-list svg { width: 12px; height: 12px; fill: var(--ink-dark); flex: none; }

  /* Product side */
  .card-product {
    display: flex; flex-direction: column; align-items: center; justify-content: center;
  }
  .product-mark {
    width: 58px; height: 58px; border-radius: 50%;
    background: linear-gradient(160deg, var(--brand-teal), var(--brand-violet));
    margin-bottom: 12px;
  }
  .product-name { font-size: 40px; font-weight: 500; color: var(--ink-dark); letter-spacing: 0.5px; }
  .product-tagline { font-size: 12px; font-weight: 700; color: var(--ink-dark); margin-top: 6px; }
  .product-site {
    display: flex; align-items: center; gap: 6px; margin-top: 10px;
    font-size: 12px; color: var(--brand-violet);
  }
  .site-rule { width: 120px; height: 8px; }
</style>
</head>
<body>
<main class="canvas">
  <section class="card card-contact" aria-label="Contact side">
    <div class="company-block">
      <div class="company-mark"></div>
      <div class="company-name">BRIGHTLOOM</div>
      <div class="company-sub">Language</div>
    </div>
    <div class="card-divider"></div>
    <div class="contact-block">
      <div class="person-name">Perry Dunmore</div>
      <div class="person-title">Founder &amp; CEO</div>
      <ul class="contact-list">
        <li>
          <svg viewBox="0 0 24 24" aria-hidden="true"><path d="M6.6 10.8a15.1 15.1 0 0 0 6.6 6.6l2.2-2.2a1 1 0 0 1 1-.25 11.4 11.4 0 0 0 3.6.57 1 1 0 0 1 1 1V20a1 1 0 0 1-1 1A17 17 0 0 1 3 4a1 1 0 0 1 1-1h3.5a1 1 0 0 1 1 1c0 1.25.2 2.45.57 3.57a1 1 0 0 1-.25 1z"/></svg>
          (555)-014-2286
        </li>
        <li>
          <svg viewBox="0 0 24 24" aria-hidden="true"><path d="M2 5h20v14H2zm2 2v.5l8 5 8-5V7zm0 2.8V17h16V9.8l-8 5z"/></svg>
          pdunmore@quillpost-mail.net
        </li>
      </ul>
    </div>
  </section>

  <section class="card card-product" aria-label="Product side">
    <div class="product-mark"></div>
    <div class="product-name">Glimworld</div>
    <div class="product-tagline">Culturally Immersive Language Learning Games</div>
    <div class="product-site">
      <svg class="site-rule" viewBox="0 0 120 8" aria-hidden="true">
        <line x1="0" y1="4" x2="114" y2="4" stroke="var(--brand-violet)" stroke-width="1"/>
        <circle cx="116" cy="4" r="2.5" fill="none" stroke="var(--brand-violet)" stroke-width="1"/>
      </svg>
      <span>www.glimworld-play.com</span>
      <svg class="site-rule" viewBox="0 0 120 8" aria-hidden="true">
        <circle cx="4" cy="4" r="2.5" fill="none" stroke="var(--brand-violet)" stroke-width="1"/>
        <line x1="6" y1="4" x2="120" y2="4" stroke="var(--brand-violet)" stroke-width="1"/>
      </svg>
    </div>
  </section>
</main>
</body>
</html>
```